Flyer for the Lumen 2025 Conference

I am looking to produce a flyer for our upcoming conference, Lumen 2025. This is an annual conference that we plan to publicize on social media. The ideal designer will create a flyer that is eye-catching and effectively communicates the key information. Please see attached our logo, speaker photo, and flyer content.

Target Market(s)

All demographics

Industry/Entity Type

Christian

Font styles to use
Sans Serif

Requirements
Should not have
• Cross, church

```html
<!DOCTYPE html>
<html lang="en">
<head>
<meta charset="utf-8">
<title>Lumen 2025 – A Prophetic Conference</title>
<link rel="stylesheet" href="https://fonts.googleapis.com/css2?family=Montserrat:wght@400;600;700;800;900&family=Poppins:wght@300;400;600;700&display=swap">
<style>
  :root {
    --navy-deep: #050d1f;
    --navy: #0a1d45;
    --royal: #0d3b9c;
    --bright-blue: #1e8be8;
    --cyan: #22c9f0;
    --gold: #e2a631;
    --gold-light: #f6d774;
    --gold-dark: #9a6a12;
    --white: #ffffff;
    --ink: #111111;
  }
  * { margin: 0; padding: 0; box-sizing: border-box; }
  html, body { width: 927px; height: 1200px; overflow: hidden; background: var(--navy-deep); }
  .flyer {
    position: relative; width: 927px; height: 1200px; overflow: hidden;
    background: radial-gradient(ellipse 70% 55% at 50% 45%, #0d2a5e 0%, var(--navy) 45%, var(--navy-deep) 100%);
    font-family: "Montserrat", sans-serif; color: var(--white);
  }
  .ornament {
    position: absolute; left: 198px; top: 63px; width: 532px; height: 530px;
    border-radius: 48% 48% 12% 12%;
    background: radial-gradient(ellipse at 50% 45%, transparent 42%, rgba(226,166,49,0.55) 52%, rgba(154,106,18,0.35) 62%, transparent 72%);
  }
  .speaker-photo {
    position: absolute; left: 239px; top: 121px; width: 428px; height: 609px;
    border-radius: 140px 140px 0 0;
    background: linear-gradient(180deg, #1a2440 0%, #4f74c0 40%, #6f93d6 70%, rgba(60,95,170,0.2) 100%);
  }
  .speaker { position: absolute; left: 31px; top: 349px; line-height: 1.05; }
  .speaker-label { font-family: "Poppins", sans-serif; font-weight: 300; font-size: 25px; color: var(--gold); }
  .speaker-name { font-weight: 800; font-size: 26px; }
  .title {
    position: absolute; left: 200px; top: 606px; width: 522px; text-align: center;
    font-weight: 900; font-size: 118px; letter-spacing: -2px; line-height: 1;
    background: linear-gradient(180deg, var(--gold-light) 0%, var(--gold) 45%, var(--gold-dark) 75%, var(--gold-light) 100%);
    -webkit-background-clip: text; background-clip: text; color: transparent;
  }
  .title-year {
    position: absolute; left: 721px; top: 620px; font-weight: 800; font-size: 38px;
    color: var(--gold);
  }
  .subtitle-box {
    position: absolute; left: 205px; top: 741px; width: 517px; height: 68px;
    border: 1.5px solid var(--gold); border-radius: 14px;
    display: flex; align-items: center; justify-content: center;
    font-family: "Poppins", sans-serif; font-weight: 700; font-size: 39px;
  }
  .topic-label { position: absolute; left: 0; width: 927px; top: 819px; text-align: center; font-family: "Poppins", sans-serif; font-weight: 300; font-size: 25px; }
  .topic-pill {
    position: absolute; left: 297px; top: 859px; width: 333px; height: 41px; border-radius: 8px;
    background: linear-gradient(90deg, var(--gold) 0%, var(--gold-light) 100%);
    display: flex; align-items: center; justify-content: center;
    font-weight: 800; font-size: 27px; color: var(--ink);
  }
  .month {
    position: absolute; left: 68px; top: 1115px; transform-origin: 0 0; transform: rotate(-90deg);
    font-weight: 800; font-size: 35px; color: var(--royal); width: 182px; text-align: center; line-height: 36px;
  }
  .schedule-row {
    position: absolute; left: 118px; width: 310px; height: 55px;
    background: linear-gradient(90deg, transparent 0%, rgba(30,139,232,0.35) 40%, var(--bright-blue) 70%, transparent 100%);
  }
  .day-number { position: absolute; left: 6px; top: 2px; font-weight: 800; font-size: 48px; color: var(--gold); line-height: 1; letter-spacing: -1px; }
  .day-number sup { font-size: 26px; vertical-align: 20px; }
  .day-name { position: absolute; left: 126px; top: 2px; font-family: "Poppins", sans-serif; font-size: 18px; }
  .day-time { position: absolute; left: 126px; top: 26px; font-weight: 700; font-size: 17px; }
  .venue-name { position: absolute; left: 523px; top: 933px; font-weight: 700; font-size: 16.5px; color: var(--gold); }
  .venue-pin { position: absolute; left: 523px; top: 958px; width: 42px; height: 39px; border-radius: 10px; background: linear-gradient(135deg, var(--bright-blue), var(--cyan)); }
  .venue-address { position: absolute; left: 576px; top: 961px; font-family: "Poppins", sans-serif; font-size: 17px; line-height: 18px; letter-spacing: 1px; }
  .divider { position: absolute; top: 1026px; height: 1.5px; background: var(--bright-blue); }
  .app-note { position: absolute; left: 524px; top: 1045px; font-family: "Poppins", sans-serif; font-size: 17px; line-height: 18px; }
  .app-note span { color: var(--bright-blue); }
  .org-name { position: absolute; left: 714px; top: 1050px; display: flex; align-items: center; gap: 8px; font-family: "Montserrat", sans-serif; font-weight: 700; font-size: 38px; color: var(--white); }
  .org-name i { display: block; width: 14px; height: 14px; border-radius: 50%; background: var(--gold); }
  .contact-bar {
    position: absolute; left: 0; top: 1134px; width: 927px; height: 30px;
    background: linear-gradient(90deg, var(--bright-blue) 0%, var(--cyan) 100%);
    font-family: "Poppins", sans-serif; font-size: 19px; color: var(--navy-deep);
  }
  .contact-item { position: absolute; top: 0; height: 30px; display: flex; align-items: center; gap: 6px; }
</style>
</head>
<body>
<main class="flyer">
  <div class="ornament" role="img" aria-label="Large golden emblem framing the speaker"></div>
  <div class="speaker-photo" role="img" aria-label="Portrait of the speaker in a light blue blazer"></div>

  <div class="speaker">
    <div class="speaker-label">SPEAKER:</div>
    <div class="speaker-name">PROPHET<br>SAMUEL OKAFOR</div>
  </div>

  <h1 class="title">LUMEN</h1>
  <div class="title-year">2025</div>
  <div class="subtitle-box">A Prophetic Conference</div>
  <div class="topic-label">Topic:</div>
  <div class="topic-pill">The Voice Of The Lord</div>

  <div class="month">December</div>
  <div class="schedule-row" style="top:933px">
    <div class="day-number">26<sup>th</sup></div>
    <div class="day-name">Friday</div>
    <div class="day-time">6:30PM - 9:00PM</div>
  </div>
  <div class="schedule-row" style="top:996px">
    <div class="day-number">27<sup>th</sup></div>
    <div class="day-name">Saturday</div>
    <div class="day-time">5:30PM - 8:00PM</div>
  </div>
  <div class="schedule-row" style="top:1059px">
    <div class="day-number">28<sup>th</sup></div>
    <div class="day-name">Sunday</div>
    <div class="day-time">4:30PM - 7:00PM</div>
  </div>

  <div class="venue-name">The Harborview Performing Arts Center</div>
  <div class="venue-pin">
    <svg width="42" height="39" viewBox="0 0 42 39" aria-hidden="true">
      <path d="M21 8c-5 0-9 4-9 9 0 6 9 14 9 14s9-8 9-14c0-5-4-9-9-9z" fill="none" stroke="#050d1f" stroke-width="3"/>
      <circle cx="21" cy="17" r="3.2" fill="#050d1f"/>
    </svg>
  </div>
  <div class="venue-address">218 Millbrook Avenue<br>Riverton, Maine 04000</div>

  <div class="divider" style="left:523px;width:184px"></div>
  <div class="divider" style="left:740px;width:117px"></div>
  <div class="app-note">Download the<br><span>KORVA App</span> to stay<br>updated on the event</div>
  <div class="org-name"><i></i>KORVA</div>

  <footer class="contact-bar">
    <div class="contact-item" style="left:70px">
      <svg width="18" height="18" viewBox="0 0 20 20" aria-hidden="true"><circle cx="10" cy="10" r="8.5" fill="none" stroke="#050d1f" stroke-width="2"/><ellipse cx="10" cy="10" rx="3.5" ry="8.5" fill="none" stroke="#050d1f" stroke-width="1.6"/><path d="M2 10h16M3.5 6h13M3.5 14h13" stroke="#050d1f" stroke-width="1.4"/></svg>
      www.korva.org
    </div>
    <div class="contact-item" style="left:360px">
      <svg width="16" height="18" viewBox="0 0 16 18" aria-hidden="true"><path d="M3 1l3 0 1.5 4-2 1.5c1 2.5 2.5 4 5 5l1.5-2 4 1.5v3c0 1-1 2-2 2C7 16 0 9 1 3c0-1 1-2 2-2z" fill="#050d1f"/></svg>
      555 014 2290
    </div>
    <div class="contact-item" style="left:620px">
      <svg width="20" height="16" viewBox="0 0 20 16" aria-hidden="true"><rect x="1" y="1" width="18" height="14" rx="2" fill="#050d1f"/><path d="M3 4l7 5 7-5" fill="none" stroke="#22c9f0" stroke-width="1.8"/></svg>
      contact@korva.org
    </div>
  </footer>
</main>
</body>
</html>
```